Laser Tattoo Removal Business Cards

We are looking for a professional business card design for a laser tattoo removal business. Ideally looking for a black business card design. The name of the business is Brightline Tattoo Removal. We place our cards at local tattoo shops so we ideally are looking for something trendy/edgy to draw both male and female clientele in.

Target Market(s)

Male/Female ages 18-60

Contact Information for Business Card

black background ideally.. hoping to stay within greys, whites and black

Font styles to use
Serif
Sans Serif

Colors
121212
a9a9a9
5c5c5c
f5f5f5
ffffff
7f7f7f
606060
848484
9d9d9d

Requirements
Must have
• Employee Info:
• Melissa Thornbury
• Chief Executive Offer
• m: 919.537.2846
• w: 919.362.4178
• f: 919.685.3907
• mthornbury@brightlinetattooremoval.example
• Address:
• 4615 Oakmere Pkwy, Suite 210
• Raleigh, NC 27654
• Website:
• www.brightlinetattooremoval.example
Nice to have
• Myabe business name on back or logo on back and employee info on the front

```html
<!DOCTYPE html>
<html lang="en">
<head>
<meta charset="utf-8">
<title>Brightline Tattoo Removal – Business Card</title>
<link href="https://fonts.googleapis.com/css2?family=Lato:wght@700&family=Arimo:wght@400&display=swap" rel="stylesheet">
<style>
  :root {
    --ink: #121212;
    --paper: #f5f5f5;
    --white: #ffffff;
    --stage: #dcdcdc;
    --rule: #121212;
    --muted: #a9a9a9;
  }
  html, body {
    margin: 0;
    width: 1200px;
    height: 900px;
    overflow: hidden;
    background: var(--stage);
  }
  .card {
    position: absolute;
    left: 150px;
    top: 172px;
    width: 900px;
    height: 556px;
    background: var(--paper);
    box-shadow: 0 10px 30px rgba(0,0,0,0.18);
    font-family: "Arimo", Arial, sans-serif;
  }
  .card__band {
    position: absolute;
    left: 0; top: 0;
    width: 900px;
    height: 311px;
    background: var(--ink);
    color: var(--white);
  }
  .brand {
    position: absolute;
    left: 231px;
    top: 155px;
    transform: translate(-50%, -50%);
    text-align: center;
    font-family: "Lato", Arial, sans-serif;
    font-weight: 700;
    color: var(--white);
    letter-spacing: 4px;
    text-transform: uppercase;
    line-height: 1.15;
    white-space: nowrap;
  }
  .brand__name { display: block; font-size: 50px; letter-spacing: 5px; }
  .brand__line { display: block; font-size: 22px; letter-spacing: 6px; margin-top: 14px; }
  .person {
    position: absolute;
    right: 69px;
    top: 62px;
    text-align: right;
  }
  .person__name {
    margin: 0;
    font-family: "Lato", Arial, sans-serif;
    font-weight: 700;
    font-size: 31px;
    text-transform: uppercase;
    letter-spacing: 0.3px;
  }
  .person__title {
    margin: 2px 0 0;
    font-size: 25px;
  }
  .phones {
    list-style: none;
    margin: 0;
    padding: 0;
    position: absolute;
    right: 69px;
    top: 172px;
    text-align: right;
    font-size: 23px;
    line-height: 35.5px;
  }
  .phones li { display: flex; align-items: center; justify-content: flex-end; gap: 12px; }
  .phones svg { width: 20px; height: 20px; fill: var(--white); }
  .card__info {
    position: absolute;
    left: 0; top: 311px;
    width: 900px;
    height: 245px;
    text-align: center;
    color: var(--ink);
  }
  .address {
    position: absolute;
    left: 0; right: 0; top: 52px;
    margin: 0;
    font-size: 26px;
    font-style: normal;
  }
  .divider {
    position: absolute;
    left: 179px;
    top: 111px;
    width: 549px;
    height: 2px;
    background: var(--rule);
  }
  .web {
    position: absolute;
    left: 0; right: 0; top: 137px;
    margin: 0;
    font-size: 24px;
    line-height: 36px;
  }
</style>
</head>
<body>
  <div class="card">
    <div class="card__band">
      <div class="brand">
        <span class="brand__name">Brightline</span>
        <span class="brand__line">Tattoo Removal</span>
      </div>
      <div class="person">
        <p class="person__name">Melissa Thornbury</p>
        <p class="person__title">Chief Executive Officer</p>
      </div>
      <ul class="phones">
        <li>919.537.2846
          <svg viewBox="0 0 20 20" aria-label="mobile"><path d="M6 1h8a2 2 0 0 1 2 2v14a2 2 0 0 1-2 2H6a2 2 0 0 1-2-2V3a2 2 0 0 1 2-2zm0 3v11h8V4zm3 12.2v1.4h2v-1.4z"/></svg>
        </li>
        <li>919.362.4178
          <svg viewBox="0 0 20 20" aria-label="phone"><path d="M4.5 1.5l3 .5 1.3 4-2 1.6a11 11 0 0 0 5.6 5.6l1.6-2 4 1.3.5 3c0 1.5-1.3 2.5-2.8 2.3C8.7 17 3 11.3 2.2 4.3 2 2.8 3 1.5 4.5 1.5z"/></svg>
        </li>
        <li>919.685.3907
          <svg viewBox="0 0 20 20" aria-label="fax"><path d="M5 1h8l2 2v4H5zM3 8h14a2 2 0 0 1 2 2v6h-3v3H4v-3H1v-6a2 2 0 0 1 2-2zm3 6v3h8v-3zm9-4v1.5h2V10z"/></svg>
        </li>
      </ul>
    </div>
    <div class="card__info">
      <address class="address">4615 Oakmere Pkwy, Suite 210 Raleigh, NC 27654</address>
      <div class="divider"></div>
      <p class="web">mthornbury@brightlinetattooremoval.example<br>www.brightlinetattooremoval.example</p>
    </div>
  </div>
</body>
</html>
```